Bright Path Mentors Needs A New Website Design

We need a 8 page website designed for "Bright Path Mentors .ca" similar in design to: "keystone learning hub .com".

The winner/successful candidate on the home page will be asked to complete the following inner pages to complete the project:

About Us
Philosophy
How We Work
Work With Us
Blog
Find A Tutor
Contact

Target Market(s)

Tutoring business clients/children

Industry/Entity Type

Education

Number of Pages Required

5+ page

Font styles to use
Sans Serif

Requirements
Must have
• The attached logo included of course. Similar design to the design provided above in the brief. Clear high quality high resolution images of children in school settings.

```html
<!DOCTYPE html>
<html lang="en">
<head>
<meta charset="utf-8">
<title>Bright Path Mentors – Home</title>
<link rel="stylesheet" href="https://fonts.googleapis.com/css2?family=Raleway:wght@400;500;600&family=Oswald:wght@400&family=Roboto:wght@400;500&display=swap">
<style>
:root{
  --orange:#f7941d;
  --blue:#2e3a97;
  --blue-dark:#26317f;
  --ink:#333;
  --muted:#777;
  --light:#f4f4f5;
  --footer:#232323;
  --footer-bottom:#111;
  --white:#fff;
}
*{box-sizing:border-box;margin:0;padding:0}
html,body{width:1200px;height:2332px;overflow:hidden;background:var(--white)}
body{position:relative;font-family:'Raleway',sans-serif;color:var(--ink)}
.abs{position:absolute}

/* header */
.site-header{top:0;left:0;width:1200px;height:78px;background:var(--white);border-bottom:2px solid var(--orange)}
.brand{left:256px;top:10px;display:flex;align-items:center;gap:8px}
.brand-mark{width:22px;height:22px;border-radius:50%;background:var(--blue)}
.brand-name{font-family:'Raleway',sans-serif;font-weight:600;font-size:15px;color:var(--blue)}
.top-bar{left:700px;top:0;width:251px;height:23px;background:var(--orange);clip-path:polygon(0 0,100% 0,100% 100%,8% 100%);display:flex;align-items:center;justify-content:flex-end;gap:9px;padding-right:14px;color:var(--white);font-size:11px;font-family:'Roboto',sans-serif}
.top-bar .dot{width:7px;height:7px;border-radius:50%;background:var(--white)}
.main-nav{right:249px;top:39px;display:flex;font-family:'Oswald',sans-serif;font-size:10.5px;color:var(--ink)}
.main-nav a{display:block;padding:0 7px;height:38px;line-height:38px;text-decoration:none;color:inherit}
.main-nav a.active{background:var(--orange);color:var(--white)}

/* hero */
.hero{top:78px;left:0;width:1200px;height:377px;background:linear-gradient(100deg,#8a7560 0%,#a9977c 30%,#c4b39a 55%,#d9c7ae 75%,#7d8f4f 100%)}
.hero-circle{left:333px;top:57px;width:264px;height:264px;border-radius:50%;background:rgba(30,30,30,.82);color:var(--white);text-align:center;padding:84px 34px 0}
.hero-circle h1{font-weight:400;font-size:15px;color:var(--orange);white-space:nowrap;margin:0 -24px}
.hero-circle h1 strong{color:var(--white);font-weight:600}
.hero-circle hr{border:0;border-top:1px solid var(--white);width:150px;margin:10px auto 9px}
.hero-circle p{font-size:8.5px;line-height:1.35}

/* feature band */
.features{top:455px;left:0;width:1200px;height:133px;background:var(--blue)}
.feature{top:0;width:234px;height:133px;padding:14px 8px 0;color:var(--white)}
.feature+.feature{border-left:1px solid rgba(255,255,255,.15)}
.feature svg{display:block;margin:0 0 6px 8px}
.feature h3{font-weight:400;font-size:15px;color:var(--orange);margin-bottom:8px}
.feature p{font-size:9px;line-height:1.3}

/* private tutoring */
.private{top:588px;left:0;width:1200px;height:279px;background:var(--light)}
.private h2{left:249px;top:24px;font-weight:400;font-size:27px;color:var(--blue)}
.private p{left:249px;top:74px;width:395px;font-size:9.5px;line-height:1.6;color:var(--muted)}
.private-photo{left:660px;top:23px;width:291px;height:244px;background:linear-gradient(135deg,#e9eef5,#c8cfd9 60%,#8a7060)}

/* services */
.services{top:867px;left:0;width:1200px;height:244px;background:linear-gradient(180deg,#2c3038,#3e4450 60%,#545a66)}
.services h2{top:36px;left:0;width:1200px;text-align:center;font-weight:400;font-size:27px;color:var(--orange)}
.service{top:96px;width:150px;text-align:center;color:var(--white)}
.service .ring{width:44px;height:44px;border-radius:50%;background:var(--white);margin:0 auto 14px;border:3px solid var(--white);display:flex;align-items:center;justify-content:center;box-shadow:0 0 0 2px var(--orange)}
.service .ring.plain{box-shadow:none}
.service h3{font-weight:400;font-size:12.5px;color:var(--orange);margin-bottom:3px}
.service p{font-size:9px;line-height:1.3}

/* promo */
.promo{top:1111px;left:0;width:1200px;height:257px;background:radial-gradient(ellipse at center,#22352b 0%,#16231c 70%,#101a14 100%)}
.promo h2{top:57px;left:0;width:1200px;text-align:center;font-weight:500;font-size:27px;color:var(--orange)}
.promo p{top:107px;left:350px;width:500px;text-align:center;font-size:9px;line-height:1.4;color:var(--white)}
.btn-outline{top:167px;left:513px;width:174px;height:39px;border:1.5px solid var(--white);border-radius:6px;color:var(--orange);font-size:16px;text-align:center;line-height:36px;letter-spacing:.5px}

/* testimonials */
.video{top:1394px;left:249px;width:376px;height:238px;border:1px solid var(--blue);background:linear-gradient(135deg,#e9dfb8,#c9c27a 40%,#a56a8a 70%,#6e7d4c)}
.play{left:160px;top:91px}
.testimonials{top:1394px;left:631px;width:320px;height:238px;background:var(--light);text-align:center}
.testimonials h2{margin-top:16px;font-weight:400;font-size:27px;color:var(--blue)}
.testimonials .who{margin-top:6px;font-size:10px;color:var(--orange)}
.testimonials .where{font-size:8.5px;color:var(--muted)}
.testimonials .quote{width:170px;margin:12px auto 0;font-size:8.5px;line-height:1.35;color:var(--muted)}
.seal{left:125px;top:134px;width:68px;height:68px;border-radius:50%;background:radial-gradient(circle,#f2c23a 0%,#c48a12 70%,#3a2a08 100%)}

/* blog */
.blog-title{top:1652px;left:0;width:1200px;text-align:center;font-weight:400;font-size:27px;color:var(--blue)}
.post{top:1694px;width:224px;height:334px;border:1px solid #ddd;background:var(--white)}
.post .photo{height:146px}
.post h3{margin:14px 0 0 9px;font-weight:400;font-size:15.5px;color:var(--blue)}
.post p{margin:6px 9px 0;font-size:8.8px;line-height:1.5;color:var(--ink)}
.post .more{position:absolute;left:-1px;bottom:-1px;width:96px;height:22px;background:var(--orange);color:var(--white);font-size:9.5px;text-align:center;line-height:22px}
.post .comment{position:absolute;right:8px;bottom:4px;font-size:8.5px;color:var(--muted);display:flex;align-items:center;gap:3px}

/* newsletter */
.newsletter{top:2047px;left:0;width:1200px;height:37px;background:var(--blue);display:flex;align-items:center;justify-content:center;gap:10px}
.newsletter span{color:var(--white);font-size:17px;margin-right:2px}
.newsletter .field{width:232px;height:18px;background:var(--white);font-size:9px;font-style:italic;color:#999;padding:3px 8px}
.newsletter .btn{margin-left:8px;width:115px;height:22px;background:var(--orange);color:var(--white);font-size:12px;text-align:center;line-height:22px}

/* footer */
.site-footer{top:2084px;left:0;width:1200px;height:248px;background:var(--footer);font-family:'Roboto',sans-serif}
.col{top:26px}
.col h4{font-family:'Raleway',sans-serif;font-weight:400;font-size:13.5px;color:var(--orange);margin-bottom:8px}
.col li{list-style:none;font-size:9.5px;color:var(--white);line-height:17.2px}
.col li.on{color:var(--orange)}
.col li::before{content:"› "}
.contact li::before{content:none}
.contact li{display:flex;align-items:center;gap:5px}
.contact .ic{width:7px;height:7px;background:var(--orange);border-radius:50%}
.social{left:882px;top:28px;text-align:center;width:86px}
.social h4{font-family:'Raleway',sans-serif;font-weight:400;font-size:13.5px;color:var(--orange);margin-bottom:10px}
.social .s{width:9px;height:9px;border-radius:50%;background:#777;margin:0 auto 14px}
.footer-bottom{top:227px;left:0;width:1200px;height:21px;background:var(--footer-bottom);color:var(--white);font-size:8px;text-align:center;line-height:21px}
</style>
</head>
<body>

<header class="site-header abs">
  <div class="brand abs"><span class="brand-mark"></span><span class="brand-name">Bright Path Mentors</span></div>
  <div class="top-bar abs"><span class="dot"></span><span class="dot"></span><span class="dot"></span><span class="dot"></span>
    <svg width="9" height="9" viewBox="0 0 24 24"><path fill="#fff" d="M6.6 10.8a15 15 0 0 0 6.6 6.6l2.2-2.2a1 1 0 0 1 1-.2 11.4 11.4 0 0 0 3.6.6 1 1 0 0 1 1 1V20a1 1 0 0 1-1 1A17 17 0 0 1 3 4a1 1 0 0 1 1-1h3.5a1 1 0 0 1 1 1c0 1.2.2 2.5.6 3.6a1 1 0 0 1-.3 1z"/></svg>
    <span>1-855-555-0142</span></div>
  <nav class="main-nav abs">
    <a class="active">Home</a><a>About Us</a><a>Philosophy</a><a>How We Work</a><a>Work With Us</a><a>Blog</a><a>Find A Tutor</a><a>Contact</a>
  </nav>
</header>

<section class="hero abs" role="img" aria-label="Smiling student with glasses on a sunny campus">
  <div class="hero-circle abs">
    <h1>Welcome to <strong>Bright Path Mentors</strong></h1>
    <hr>
    <p>Lorem Ipsum is simply dummy text of the printing and typesetting industry. Lorem Ipsum has been the industry's standard dummy text ever since the 1500s, when an unknown printer took a galley of type and scrambled it to make a type specimen book. It has survived not only five</p>
  </div>
</section>

<section class="features abs">
  <div class="feature abs" style="left:249px">
    <svg width="22" height="20" viewBox="0 0 22 20"><rect x="2" y="1" width="18" height="12" fill="none" stroke="#fff" stroke-width="1.5"/><circle cx="7" cy="16" r="2" fill="#fff"/><rect x="4" y="18" width="6" height="2" fill="#fff"/></svg>
    <h3>How We Operate</h3>
    <p>Lorem Ipsum is simply dummy text of the printing andtypesetting industry. Lorem Ipsum has been the industry's standard dummy text ever since the 1500s, when an unknown printer took a galley of type and</p>
  </div>
  <div class="feature abs" style="left:483px">
    <svg width="22" height="20" viewBox="0 0 22 20"><rect x="1" y="1" width="20" height="14" rx="2" fill="none" stroke="#fff" stroke-width="1.5"/><circle cx="11" cy="7" r="3" fill="#fff"/><rect x="6" y="17" width="10" height="2" fill="#fff"/></svg>
    <h3>Tutor Selection Process</h3>
    <p>Lorem Ipsum is simply dummy text of the andtypesetting industry. Lorem Ipsum has industry's standard dummy text ever since the 1500s, when an unknown printer took a galley of type and</p>
  </div>
  <div class="feature abs" style="left:717px">
    <svg width="22" height="20" viewBox="0 0 22 20"><rect x="1" y="1" width="16" height="11" fill="none" stroke="#fff" stroke-width="1.5"/><rect x="4" y="14" width="10" height="2" fill="#fff"/><circle cx="18" cy="15" r="3" fill="none" stroke="#fff" stroke-width="1.5"/></svg>
    <h3>Online Tutoring</h3>
    <p>Lorem Ipsum is simply dummy text of the printing andtypesetting industry. Lorem Ipsum has been the industry's standard dummy text ever since the 1500s, when an unknown printer took a galley of type and</p>
  </div>
</section>

<section class="private abs">
  <h2 class="abs">Private Home Tutoring</h2>
  <p class="abs">Lorem Ipsum is simply dummy text of the printing and typesetting industry. Lorem Ipsum has been the industry's standard dummy text ever since the 1500s, when an unknown printer took a galley of type and scrambled it to make a type specimen book. It has survived not only five centuries, but also the leap into electronic typesetting, remaining essentially unchanged. It was popularised in the 1960s with the release of Letraset sheets containing Lorem Ipsum passages, and more recently with desktop publishing software like Aldus PageMaker including versions of Lorem Ipsum.</p>
  <div class="private-photo abs" role="img" aria-label="Student writing at a classroom desk with classmates behind"></div>
</section>

<section class="services abs" role="img" aria-label="Graduates tossing caps into the air">
  <h2 class="abs">Our Services</h2>
  <div class="service abs" style="left:239px"><div class="ring plain"><svg width="18" height="18" viewBox="0 0 18 18"><rect x="2" y="2" width="14" height="10" fill="none" stroke="#2e3a97" stroke-width="1.6"/><rect x="5" y="14" width="8" height="2" fill="#2e3a97"/></svg></div><h3>Home Tutors</h3><p>Lorem Ipsum is simply dummy text of the printing and typesetting industry. Lorem Ipsum has been1500s, when</p></div>
  <div class="service abs" style="left:432px"><div class="ring"><svg width="18" height="18" viewBox="0 0 18 18"><rect x="2" y="5" width="10" height="8" rx="1" fill="#2e3a97"/><path d="M12 8l4-2v6l-4-2z" fill="#2e3a97"/></svg></div><h3>Video Tutorial</h3><p>Lorem Ipsum is simply dummy text of the printing and typesetting industry. Lorem Ipsum has been1500s, when</p></div>
  <div class="service abs" style="left:625px"><div class="ring"><svg width="18" height="18" viewBox="0 0 18 18"><rect x="2" y="3" width="14" height="10" fill="none" stroke="#2e3a97" stroke-width="1.6"/><rect x="5" y="6" width="8" height="4" fill="#2e3a97"/></svg></div><h3>Online Education</h3><p>Lorem Ipsum is simply dummy text of the printing and typesetting industry. Lorem Ipsum has been1500s, when</p></div>
  <div class="service abs" style="left:811px"><div class="ring"><svg width="18" height="18" viewBox="0 0 18 18"><path d="M3 15L15 3M6 4l8 8" stroke="#2e3a97" stroke-width="2"/></svg></div><h3>All Education</h3><p>Lorem Ipsum is simply dummy text of the printing and typesetting industry. Lorem Ipsum has been1500s, when</p></div>
</section>

<section class="promo abs">
  <h2 class="abs">FIRST SESSION JUST $7! All SUBJECTS! ALL GRADES!</h2>
  <p class="abs">Lorem Ipsum is simply dummy text of the printing and typesetting industry Lorem Ipsum has been the industry's standard dummy text ever since the 1500s, when an unknown printer took a galley of type and scrambled it to make a type specimen book. It has survived not only five centuries, but also the leap into electronic typesetting.</p>
  <div class="btn-outline abs">BOOK NOW</div>
</section>

<div class="video abs" role="img" aria-label="Student holding a phone and books outdoors, video thumbnail">
  <svg class="play abs" width="56" height="56" viewBox="0 0 56 56"><circle cx="28" cy="28" r="25" fill="rgba(255,255,255,.2)" stroke="#fff" stroke-width="3"/><path d="M22 17l17 11-17 11z" fill="#fff"/></svg>
</div>
<section class="testimonials abs">
  <h2>Our Testimonials</h2>
  <div class="who">Dana M.</div>
  <div class="where">Vaughan, Ontario</div>
  <p class="quote">Clara Westwood Dear Ms. Westwood RE: Highest Recommendation for Tutoring Services: I take this opportunity to give the highest...</p>
  <div class="seal abs" role="img" aria-label="Guarantee seal"></div>
</section>

<h2 class="blog-title abs">Our Blog</h2>
<article class="post abs" style="left:249px">
  <div class="photo" role="img" aria-label="Young man peeking over a stack of books" style="background:linear-gradient(135deg,#6b3a1e,#b46a3c 50%,#e8e3dc)"></div>
  <h3>Online Education</h3>
  <p>Lorem Ipsum is simply dummy text of the printing and typesetting industry. Lorem Ipsum has been the industry's standard dummy text ever since the 1500s, when an unknown printer took a galley of type and scrambled it to make a type specimen book. It has survived not only five centuries, but also the leap into electronic typesetting, remaining essentially unchanged. It was popularised in the 1960s with the</p>
  <div class="more">READ MORE</div><div class="comment">● comment</div>
</article>
<article class="post abs" style="left:488px">
  <div class="photo" role="img" aria-label="Smiling student holding a folder" style="background:linear-gradient(135deg,#f2f2f2,#d9d4d0 50%,#5a4a44)"></div>
  <h3>Online Education</h3>
  <p>Lorem Ipsum is simply dummy text of the printing and typesetting industry. Lorem Ipsum has been the industry's standard dummy text ever since the 1500s, when an unknown printer took a galley of type and scrambled it to make a type specimen book. It has survived not only five centuries, but also the leap into electronic typesetting, remaining essentially unchanged. It was popularised in the 1960s with the</p>
  <div class="more">READ MORE</div><div class="comment">● comment</div>
</article>
<article class="post abs" style="left:727px">
  <div class="photo" role="img" aria-label="Two happy children in a classroom" style="background:linear-gradient(135deg,#f0e6d2,#e3b774 50%,#d99a3e)"></div>
  <h3>Online Education</h3>
  <p>Lorem Ipsum is simply dummy text of the printing and typesetting industry. Lorem Ipsum has been the industry's standard dummy text ever since the 1500s, when an unknown printer took a galley of type and scrambled it to make a type specimen book. It has survived not only five centuries, but also the leap into electronic typesetting, remaining essentially unchanged. It was popularised in the 1960s with the</p>
  <div class="more">READ MORE</div><div class="comment">● comment</div>
</article>

<section class="newsletter abs">
  <span>Subscribe to Olur Newsletter :</span>
  <div class="field">Enter Email</div>
  <div class="btn">Subscribe</div>
</section>

<footer class="site-footer abs">
  <div class="col abs" style="left:249px"><h4>Site Map</h4><ul><li class="on">Home</li><li>About Us</li><li>Philosophy</li><li>How We Work</li><li>Work With Us</li><li>Blog</li><li>Find A Tutor</li><li>Contact</li></ul></div>
  <div class="col abs" style="left:374px"><h4>Subjects</h4><ul><li>Elementary Tutoring</li><li>Foreign Languages</li><li>Math Tutoring</li><li>Science Tutoring</li></ul></div>
  <div class="col abs" style="left:520px"><h4>Other Subjects</h4><ul><li>Elementary Math Tutoring</li><li>Elementary Tutoring</li><li>Foreign Languages</li><li>Elementary Math Tutoring</li><li>Elementary School Math</li><li>Online Tutoring</li><li>Phonics Tutoring</li><li>Reading Tutoring</li><li>Biology Tutoring</li></ul></div>
  <div class="col contact abs" style="left:697px"><h4>Contact</h4><ul><li><span class="ic"></span>1200 Maple Avenue, Suite 210</li><li><span class="ic"></span>Toronto</li><li><span class="ic"></span>Ontario</li><li><span class="ic"></span>M4B 1Z9</li><li><span class="ic"></span>1-855-555-0142</li><li><span class="ic"></span>info@brightpathmentors.ca</li></ul></div>
  <div class="social abs"><h4>Social Media</h4><div class="s"></div><div class="s"></div><div class="s"></div><div class="s"></div></div>
  <div class="footer-bottom abs">© 2016 All Rights Bright Path Mentors</div>
</footer>

</body>
</html>
```